Wine Label

I need a label for my home made red wine. I name it Merivane Heritage, I want a vintage design with an "Ouroboros encircled around a Sowilo rune" incorporated in the design

```html
<!DOCTYPE html>
<html lang="en">
<head>
<meta charset="utf-8">
<title>Merivane Heritage — Wine Label</title>
<link href="https://fonts.googleapis.com/css2?family=Rubik+Dirt&display=swap" rel="stylesheet">
<style>
  :root {
    --paper: #ffffff;
    --gold: #cca03f;
    --kraft: #b09573;
    --ink: #353333;
  }
  html, body {
    margin: 0;
    padding: 0;
    width: 1200px;
    height: 849px;
    overflow: hidden;
    background: var(--paper);
  }
  .sheet { display: block; width: 1200px; height: 849px; }
  .wordmark {
    font-family: "Rubik Dirt", "Impact", sans-serif;
    text-anchor: middle;
  }
  .label-gold .wordmark, .label-gold .mark-name { fill: var(--gold); }
  .label-kraft .wordmark, .label-kraft .mark-name { fill: var(--ink); }
  .mark-name {
    font-family: "Rubik Dirt", "Impact", sans-serif;
    font-size: 30px;
    text-anchor: middle;
  }
</style>
</head>
<body>
<svg class="sheet" viewBox="0 0 2339 1654" xmlns="http://www.w3.org/2000/svg">
  <defs>
    <path id="label-outer" d="M592 250 C545 250 535 280 533 281 C490 300 482 330 478 340 C472 352 448 362 448 362 H388 V384 H350 V416 H322 V440 C305 446 292 458 292 458 C200 475 140 530 140 600 V1230 C140 1310 220 1360 315 1370 C325 1385 350 1398 380 1398 C420 1398 465 1375 480 1375 C492 1375 497 1388 505 1400 C525 1420 550 1425 567 1425 C580 1428 605 1428 618 1425 C640 1425 665 1418 685 1400 C693 1388 698 1375 710 1375 C725 1375 770 1398 810 1398 C840 1398 862 1385 870 1370 C965 1360 1045 1310 1045 1230 V600 C1045 530 985 475 892 458 C892 458 880 446 862 440 V416 H834 V384 H796 V362 H736 C736 362 712 352 706 340 C702 330 694 300 651 281 C649 280 639 250 592 250 Z"/>
    <path id="label-inner" d="M568 297 C568 280 616 280 614 297 C650 310 660 330 665 345 C672 365 705 378 726 388 H756 V410 H793 V443 H822 V462 C850 464 862 475 867 483 C950 495 1004 540 1004 598 V1232 C1004 1300 935 1345 835 1345 V1352 C835 1368 815 1370 805 1370 C770 1370 730 1345 690 1345 C660 1345 645 1365 635 1380 C625 1395 610 1400 600 1398 C592 1400 584 1398 578 1398 C570 1400 555 1395 545 1380 C535 1365 520 1345 490 1345 C450 1345 410 1370 375 1370 C365 1370 349 1368 349 1352 V1345 C250 1345 180 1300 180 1232 V598 C180 540 235 495 318 483 C323 475 335 464 362 462 V443 H391 V410 H428 V388 H458 C480 378 512 365 519 345 C524 330 534 310 568 297 Z"/>
  </defs>

  <!-- Gold variant -->
  <g class="label-gold">
    <rect x="80" y="207" width="1040" height="1263" rx="40" fill="var(--gold)"/>
    <use href="#label-outer" fill="var(--ink)"/>
    <use href="#label-inner" fill="none" stroke="var(--gold)" stroke-width="6"/>
    <g class="brand-mark">
      <circle cx="592" cy="445" r="80" fill="none" stroke="var(--gold)" stroke-width="14"/>
      <text class="mark-name" x="592" y="455">MERIVANE</text>
    </g>
    <text class="wordmark" x="592" y="800" font-size="250" textLength="660" lengthAdjust="spacingAndGlyphs">MERIVANE</text>
    <text class="wordmark" x="592" y="898" font-size="88" textLength="400" lengthAdjust="spacingAndGlyphs">HERITAGE</text>
    <rect role="img" aria-label="Celtic knotwork ornament of two interlaced serpents" x="295" y="928" width="600" height="318" rx="120" fill="var(--gold)"/>
    <rect role="img" aria-label="small filigree flourish with a star" x="490" y="1282" width="200" height="68" rx="34" fill="var(--gold)" opacity="0.8"/>
  </g>

  <!-- Kraft variant -->
  <g class="label-kraft">
    <rect x="1146" y="209" width="1040" height="1263" rx="40" fill="var(--kraft)"/>
    <g transform="translate(1066 2)">
      <use href="#label-outer" fill="none" stroke="var(--ink)" stroke-width="3"/>
      <use href="#label-outer" fill="none" stroke="var(--ink)" stroke-width="1.5" transform="translate(592 840) scale(0.978) translate(-592 -840)"/>
      <use href="#label-inner" fill="none" stroke="var(--ink)" stroke-width="7"/>
      <g class="brand-mark">
        <circle cx="592" cy="445" r="80" fill="none" stroke="var(--ink)" stroke-width="14"/>
        <text class="mark-name" x="592" y="455">MERIVANE</text>
      </g>
      <text class="wordmark" x="592" y="800" font-size="250" textLength="660" lengthAdjust="spacingAndGlyphs">MERIVANE</text>
      <text class="wordmark" x="592" y="898" font-size="88" textLength="400" lengthAdjust="spacingAndGlyphs">HERITAGE</text>
      <rect role="img" aria-label="Celtic knotwork ornament of two interlaced serpents" x="295" y="928" width="600" height="318" rx="120" fill="var(--ink)"/>
      <rect role="img" aria-label="small filigree flourish with a star" x="490" y="1282" width="200" height="68" rx="34" fill="var(--ink)" opacity="0.8"/>
    </g>
  </g>
</svg>
</body>
</html>
```